sydney wedding photography business needs a business card design

we need a business card design for a sydney based wedding photography and videography business. our business name is :golden hour studio and film. our target clients are 24-35 yrs female. our style is candid, organic, natural, dynamic. we are a team of young photographers and videographers, and help brides to create memories that they will cherish for the rest of their lives. the logo will be provided. we want an elegant design that reflects our style, and also want to give a great impression to our clients that we are one of the best studios in sydney and our brand means quality and premium service.

Target Market(s)

bride to be, 24-35 years old, living in sydney and surrunding areas

Industry/Entity Type

Wedding Photography

Contact Information for Business Card

address: 57 tarrant street, glenmore nsw 2047
mobile: 0431872259
phone: (02) 9163 2408
info@tidewillowstudio.net.au
www.tidewillowstudio.net.au
facebook:tidewillowweddings
instagram:tidewillowweddings

Font styles to use
Serif
Sans Serif

Requirements
Nice to have
• maybe add my slogan"memories beyond eternity" if the layout looks good
Should not have
• no black color, not good idea for wedding biz card

```html
<!DOCTYPE html>
<html lang="en">
<head>
<meta charset="UTF-8">
<title>Golden Hour Studio and Film — Business Card</title>
<link href="https://fonts.googleapis.com/css2?family=Oswald:wght@300;400;500&display=swap" rel="stylesheet">
<style>
  :root {
    --paper: #ece8e0;
    --espresso: #3d2a12;
    --espresso-deep: #2f200d;
    --ink: #3a2810;
    --gold-light: #dca814;
    --gold: #c3900f;
    --gold-deep: #9c6d0c;
    --shadow: rgba(60, 45, 10, 0.28);
  }
  * { margin: 0; padding: 0; box-sizing: border-box; }
  html, body {
    width: 1200px;
    height: 774px;
    overflow: hidden;
    background: var(--paper);
    font-family: "Oswald", "Arial Narrow", sans-serif;
  }
  .stage {
    position: relative;
    width: 1200px;
    height: 774px;
    display: flex;
    align-items: center;
    justify-content: center;
    gap: 60px;
  }
  .card {
    position: relative;
    width: 520px;
    height: 300px;
    overflow: hidden;
    box-shadow: 0 10px 24px var(--shadow);
  }

  /* Back side */
  .card--back {
    background: radial-gradient(ellipse at 50% 40%, var(--gold-light) 0%, var(--gold) 55%, var(--gold-deep) 100%);
    display: flex;
    align-items: center;
    justify-content: center;
  }
  .back-name {
    margin-top: -20px;
    font-weight: 400;
    font-size: 22px;
    letter-spacing: 0.12em;
    text-transform: uppercase;
    color: var(--ink);
  }
  .social-handle {
    position: absolute;
    bottom: 38px;
    left: 0;
    right: 0;
    display: flex;
    justify-content: center;
    align-items: center;
    gap: 7px;
    font-weight: 300;
    font-size: 14px;
    color: var(--ink);
  }
  .social-handle__dot {
    width: 12px;
    height: 12px;
    border-radius: 50%;
    background: var(--ink);
  }

  /* Front side */
  .card--front {
    background: linear-gradient(160deg, var(--espresso) 0%, var(--espresso-deep) 100%);
  }
  .front-top {
    position: absolute;
    top: 0; left: 0; right: 0;
    height: 185px;
    display: flex;
    align-items: center;
    justify-content: center;
  }
  .brand-name {
    font-weight: 500;
    font-size: 30px;
    letter-spacing: 0.08em;
    text-transform: uppercase;
    color: var(--gold-light);
  }
  .front-band {
    position: absolute;
    left: 0; right: 0; bottom: 0;
    height: 115px;
    background: linear-gradient(100deg, var(--gold-deep) 0%, var(--gold) 45%, var(--gold-light) 100%);
  }
  .holder {
    position: absolute;
    top: 14px;
    right: 62px;
    font-weight: 400;
    font-size: 16px;
    letter-spacing: 0.02em;
    color: var(--ink);
    text-transform: uppercase;
  }
  .holder__role { font-weight: 300; }
  .contact-row {
    position: absolute;
    left: 24px; right: 18px; bottom: 18px;
    display: flex;
    align-items: flex-end;
    justify-content: space-between;
    text-transform: uppercase;
    font-weight: 300;
    font-size: 12px;
    line-height: 1.35;
    color: var(--ink);
  }
  .contact-col { padding: 0 10px; }
  .contact-col + .contact-col {
    border-left: 1px solid rgba(58, 40, 16, 0.5);
  }
  .contact-col b { font-weight: 500; }

  .corner-marks {
    position: absolute;
    inset: 0;
    pointer-events: none;
  }
</style>
</head>
<body>
<main class="stage">

  <section class="card card--back" aria-label="Card back">
    <div class="back-name">golden hour studio and film</div>
    <div class="social-handle">
      <span class="social-handle__dot"></span>
      <span>tidewillowweddings</span>
    </div>
  </section>

  <section class="card card--front" aria-label="Card front">
    <div class="front-top">
      <div class="brand-name">golden hour studio and film</div>
    </div>

    <div class="front-band">
      <div class="holder">Mara Ellison – <span class="holder__role">CEO/Founder</span></div>
      <div class="contact-row">
        <div class="contact-col">
          57 Tarrant Street<br>Glenmore NSW 2047
        </div>
        <div class="contact-col">
          <b>Phone</b> : (02) 9163 2408<br><b>Cell</b> : (04) 3187 2259
        </div>
        <div class="contact-col">
          info@tidewillowstudio.net.au<br>www.tidewillowstudio.net.au
        </div>
      </div>
    </div>

    <svg class="corner-marks" width="520" height="300" viewBox="0 0 520 300" aria-hidden="true">
      <g fill="none" stroke="#dca814" stroke-width="1.5">
        <polyline points="14,36 14,14 36,14"/>
        <polyline points="484,14 506,14 506,36"/>
        <polyline points="14,150 14,172 36,172"/>
        <polyline points="506,150 506,172 484,172"/>
      </g>
    </svg>
  </section>

</main>
</body>
</html>
```